New Business Card Design Project

I'd like a business card design around the same modern style that I used on my website www.brovanhs.com
It's gonna be one of those round corners double-sided business cards with maybe a big logo on the front and all the info on the back of the card.

Contact Information for Business Card

Marco Delgado
425-317-6084
www.brovanhs.com

www.facebook.com/BrovanHomeServices
www.intsgram.com/BrovanHomeServices

Requirements
Must have
• it needs to look elegant and modern

```html
<!DOCTYPE html>
<html lang="en">
<head>
<meta charset="utf-8">
<title>Brovan Home Services – Business Card</title>
<link rel="stylesheet" href="https://fonts.googleapis.com/css2?family=Work+Sans:wght@400;500;600&display=swap">
<style>
  :root {
    --page-bg: #e4e5e8;
    --card-dark: #2a2a2d;
    --card-light: #ffffff;
    --brand-blue: #1a86d6;
    --ink: #1f1f22;
    --muted: #3a3a3e;
  }
  * { box-sizing: border-box; margin: 0; padding: 0; }
  html, body { width: 1200px; height: 900px; overflow: hidden; }
  body {
    background: var(--page-bg);
    font-family: "Work Sans", Arial, sans-serif;
    display: flex;
    flex-direction: column;
    align-items: center;
    justify-content: center;
    gap: 60px;
  }
  .card {
    width: 525px;
    height: 300px;
    border-radius: 18px;
    box-shadow: 0 10px 30px rgba(0,0,0,0.18);
    position: relative;
    overflow: hidden;
  }
  .card--front {
    background: var(--card-dark);
    display: flex;
    align-items: center;
    justify-content: center;
  }
  .brand {
    display: flex;
    align-items: center;
    gap: 14px;
  }
  .brand__dot {
    width: 22px; height: 22px; border-radius: 50%;
    background: var(--brand-blue);
  }
  .brand__name {
    color: var(--brand-blue);
    font-weight: 600;
    font-size: 34px;
    letter-spacing: 0.5px;
  }
  .card--back {
    background: linear-gradient(160deg, #f1f1f2 0%, #ffffff 55%, #f3f3f4 100%);
    display: flex;
    align-items: center;
    justify-content: center;
    gap: 26px;
  }
  .identity { text-align: right; }
  .identity__name {
    color: var(--brand-blue);
    font-weight: 500;
    font-size: 27px;
    letter-spacing: 1px;
    text-transform: uppercase;
  }
  .identity__role {
    font-size: 16px;
    color: var(--muted);
    margin: 2px 0 10px;
  }
  .identity__address {
    font-size: 13px;
    line-height: 1.45;
    color: var(--ink);
  }
  .divider {
    width: 2px; height: 104px;
    background: var(--brand-blue);
    margin-top: 50px;
  }
  .contacts {
    list-style: none;
    margin-top: 78px;
    font-size: 14px;
    line-height: 1.55;
    color: var(--ink);
  }
  .contacts li { display: flex; align-items: center; gap: 8px; }
  .contacts svg { width: 11px; height: 11px; flex: none; }
  .social-dot {
    width: 9px; height: 9px; border-radius: 50%;
    background: var(--brand-blue); flex: none; margin: 0 1px;
  }
</style>
</head>
<body>
  <section class="card card--front" aria-label="Card front">
    <div class="brand">
      <span class="brand__dot"></span>
      <span class="brand__name">Brovan Home Services</span>
    </div>
  </section>

  <section class="card card--back" aria-label="Card back">
    <div class="identity">
      <p class="identity__name">Marco Delgado</p>
      <p class="identity__role">Director</p>
      <p class="identity__address">2417 Larkspur Hollow Road<br>Tulsa, OK 74105</p>
    </div>
    <div class="divider"></div>
    <ul class="contacts">
      <li>
        <svg viewBox="0 0 12 12" aria-hidden="true"><path d="M2.5 1 L4.5 1 L5.2 3.6 L3.9 4.6 Q5 7 7.4 8.1 L8.4 6.8 L11 7.5 L11 9.5 Q11 11 9.5 11 Q1 10 1 2.5 Q1 1 2.5 1Z" fill="var(--brand-blue)"/></svg>
        425-317-6084
      </li>
      <li>
        <svg viewBox="0 0 12 12" aria-hidden="true"><rect x="1" y="2.5" width="10" height="7" fill="none" stroke="var(--brand-blue)" stroke-width="1.3"/><path d="M1 2.5 L6 6.5 L11 2.5" fill="none" stroke="var(--brand-blue)" stroke-width="1.3"/></svg>
        info@brovanhs.com
      </li>
      <li>
        <svg viewBox="0 0 12 12" aria-hidden="true"><circle cx="6" cy="6" r="5" fill="none" stroke="var(--brand-blue)" stroke-width="1.2"/><ellipse cx="6" cy="6" rx="2.2" ry="5" fill="none" stroke="var(--brand-blue)" stroke-width="1"/><path d="M1 6 H11" stroke="var(--brand-blue)" stroke-width="1"/></svg>
        www.brovanhs.com
      </li>
      <li><span class="social-dot"></span>/BrovanHomeServices</li>
      <li><span class="social-dot"></span>/BrovanHomeServices</li>
    </ul>
  </section>
</body>
</html>
```